Corporate Branded Documents - IT Provider - On-going work

Hi, I'm Ned a Director of Harbourlane ICT Support a UK Based IT & Telecoms support firm. We've been trading for 12 years now and feel its time for a lick of paint. We have a logo, website etc but would like someone to create some standard documents for us.

- A PDF Proposal Template - We currently don't send our customers proposals as we have nothing that looks good.
- A Quote Template PDF - Example Attached
- A Order Template PDF - Example Attached
- A Invoice Template PDF - Example Attached
- A Generic Document PDF - Something we can use for customer application forms, NDA Agreements, Terms & Conditions etc

Our website can be found at www.harbourlaneictsupport.co.uk - here you'll get a feel for our branding. I've also attached 2 example documents - as well as our currently used documents. Hopefully you guys can see why it needs improving.

We'd also like to work with someone long term, these documents are a start but we'd like to make sure all the work we do looks and feels as smart as possible, so there is plenty of additional work available.

None of these templates need to be Print ready, 99% of the time it will be viewed digitally, so high resolution designs are best

Thanks,

Ned

Target Market(s)

Corporate & Educational Customers

Industry/Entity Type

It Support

Font styles to use
Sans Serif

Colors
ec1f27
0692cd
ffffff

```html
<!DOCTYPE html>
<html lang="en">
<head>
<meta charset="utf-8">
<title>Harbourlane ICT Support – Document Templates</title>
<link href="https://fonts.googleapis.com/css2?family=Open+Sans:ital,wght@0,400;0,600;0,700;1,400&display=swap" rel="stylesheet">
<style>
:root{
  --teal:#17879e;
  --teal-soft:#2a9ab2;
  --red:#d8262e;
  --ink:#2f3338;
  --grey:#6b6f73;
  --panel:#ececec;
  --row-alt:#eef3f5;
  --paper:#ffffff;
  --stage:#000000;
}
*{box-sizing:border-box;margin:0;padding:0}
html,body{width:1200px;height:1118px;overflow:hidden;background:var(--stage);font-family:"Open Sans",Arial,sans-serif;color:var(--ink)}
.sheet{position:absolute;width:379px;height:533px;background:var(--paper);overflow:hidden}
.r1{top:13px}.r2{top:566px}
.c1{left:10px}.c2{left:409px}.c3{left:805px}

.brand{position:absolute;color:var(--teal);font-weight:600;font-size:9px;line-height:1;white-space:nowrap}
.brand.large{font-size:17px}
.brand.white{color:#fff}

.abs{position:absolute}
.body{font-size:8px;line-height:14px;color:var(--grey);text-align:justify;overflow:hidden}
.subtitle{color:var(--teal);font-weight:600}
.footer{position:absolute;right:14px;top:512px;font-size:8px;color:var(--grey);display:flex;align-items:center;gap:6px}
.footer b{font-weight:600;color:var(--ink);border-left:1px solid #bbb;padding-left:6px}

/* cover */
.cover .date{right:23px;top:12px;font-size:11px;color:var(--teal);letter-spacing:.5px}
.cover .band{left:0;top:154px;width:100%;height:379px;background:var(--teal);border-top:3px solid var(--red)}
.cover .title{right:24px;top:184px;font-size:26px;font-weight:700;color:#fff;text-align:right}
.cover .desc{right:24px;top:226px;font-size:12px;color:#fff}

/* headings sheet */
.h{left:24px;position:absolute;font-weight:600}
.h1{top:68px;font-size:22px;color:var(--teal)}
.h2{top:109px;font-size:19px;color:var(--teal)}
.h3{top:150px;font-size:16px}
.h4{top:191px;font-size:13.5px}
.h5{top:231px;font-size:12px}
.sub-red{left:25px;top:258px;font-size:10px;font-weight:700;color:var(--red)}
.lead{left:25px;top:283px;width:335px;font-size:11px;line-height:16.2px;color:var(--grey)}
.quote{left:26px;top:361px;width:330px;font-size:11px;line-height:15.5px;color:var(--red);font-style:italic}
.fine{left:25px;top:418px;width:345px;font-size:7.6px;line-height:13.2px;color:var(--grey)}

/* intro sheet */
.topband{left:0;top:0;width:100%;height:34px;background:var(--teal)}
.intro-a{left:19px;top:65px;width:340px;font-size:10px;line-height:16px;color:var(--teal);font-weight:600}
.intro-b{left:19px;top:108px;width:340px;font-size:10px;line-height:16px;color:var(--ink);font-weight:600}
.intro-c{left:19px;top:150px;width:345px;font-size:8.6px;line-height:14.6px;color:var(--grey)}
.redband{left:0;top:517px;width:100%;height:16px;background:var(--red);color:#fff;font-size:7.5px;display:flex;justify-content:space-between;align-items:center;padding:0 6px}

/* table */
.table{left:13px;top:172px;width:350px;border-collapse:collapse;font-size:9px;position:absolute}
.table th{background:var(--teal);color:#fff;font-weight:600;text-align:left;height:20px;padding:0 6px}
.table td{height:26.4px;padding:0 6px;color:var(--grey)}
.table tr:nth-child(even) td{background:var(--row-alt)}
.table .price{text-align:right;padding-right:16px}

/* panels */
.greybox{left:201px;top:123px;width:158px;height:199px;background:var(--panel);padding:10px 12px;font-size:8px;line-height:14px;font-style:italic;color:var(--ink);text-align:justify}
.redbar{left:0;top:10px;width:289px;height:10px;background:var(--red)}
.tealbox{left:6px;top:163px;width:150px;height:304px;background:var(--teal-soft);color:#fff;font-size:8px;line-height:17px;font-style:italic;text-align:center;display:flex;align-items:center;padding:0 8px}
.tealfoot{left:0;top:510px;width:297px;height:23px;background:var(--teal)}
</style>
</head>
<body>

<!-- Cover -->
<section class="sheet r1 c1 cover">
  <div class="abs date">JULY 2018</div>
  <div class="brand large" style="right:23px;top:108px">Harbourlane ICT Support</div>
  <div class="abs band"></div>
  <div class="abs title">Project Title Here</div>
  <div class="abs desc">Some Description Here</div>
</section>

<!-- Heading styles -->
<section class="sheet r1 c2">
  <div class="brand" style="right:10px;top:17px">Harbourlane ICT Support</div>
  <div class="h h1">H1 Heading Here</div>
  <div class="h h2">H2 Heading Here</div>
  <div class="h h3">H3 Heading Here</div>
  <div class="h h4">H4 Heading Here</div>
  <div class="h h5">H5 Heading Here</div>
  <div class="abs sub-red">Subsection Heading Text</div>
  <p class="abs lead">Lorem Ipsum is simply dummy text of the printing and typesetting industry. Lorem Ipsum has been the industry's industry. Lorem Ipsum has been the finishLorem Ipsum is simply dummy text of the printing and typesetting industry.</p>
  <p class="abs quote">Lorem Ipsum has been the industry's industry. Lorem Ipsum has been the finishLorem Ipsum is simply dummy text of the printing and typesetting industry.</p>
  <p class="abs fine">Lorem Ipsum is simply dummy text of the printing and typesetting industry. Lorem Ipsum has been the industry's industry. Lorem Ipsum has been the finishLorem Ipsum is simply dummy text of the printing and typesetting industry. Lorem Ipsum is simply dummy text of the printing and typesetting industry. Lorem Ipsum has been the industry's industry. Lorem Ipsum has been the finishLorem Ipsum is simply dummy text of the printing and typesetting industry.</p>
  <div class="footer">Confendtial <b>1</b></div>
</section>

<!-- Intro with columns -->
<section class="sheet r1 c3">
  <div class="abs topband"></div>
  <div class="brand white" style="right:10px;top:13px">Harbourlane ICT Support</div>
  <p class="abs intro-a">Lorem Ipsum is simply dummy text of the printing and typesetting industry typesetting industry</p>
  <p class="abs intro-b">Lorem Ipsum is simply dummy text of the printing and typesetting industry typesetting industry</p>
  <p class="abs intro-c">Lorem Ipsum is simply dummy text of the printing and typesetting industry. Lorem Ipsum has been the industry's industry. Lorem Ipsum has been the finishLorem Ipsum is simply dummy text of the printing and typesetting industry. Lorem Ipsum has been the industry's industry. Lorem Ipsum has been the finish</p>
  <div class="abs" style="left:21px;top:231px;width:155px">
    <div class="subtitle" style="font-size:10px;line-height:14px">Subtitle Here</div>
    <p class="body" style="height:224px">Lorem Ipsum is simply dummy text of the printing and typesetting industry. Lorem Ipsum has been the industry's industry. Lorem Ipsum has been the finishLorem Ipsum is simply dummy text of the printing and typesetting industry. Lorem Ipsum has been the industry's industry. Lorem Ipsum has been the finishLorem Ipsum is simply dummy text of the printing and typesetting industry. Lorem Ipsum has been the industry's industry. Lorem Ipsum has been the finishLorem Ipsum is simply dummy text of the printing and typesetting industry. Lorem Ipsum has been the industry's industry. Lorem Ipsum has been the finish.</p>
  </div>
  <div class="abs" style="left:205px;top:231px;width:155px">
    <p class="body" style="height:252px">Lorem Ipsum is simply dummy text of the printing and typesetting industry. Lorem Ipsum has been the industry's industry. Lorem Ipsum has been the finishLorem Ipsum is simply dummy text of the printing and typesetting industry. Lorem Ipsum has been the industry's industry. Lorem Ipsum has been the finishLorem Ipsum is simply dummy text of the printing and typesetting industry. Lorem Ipsum has been the industry's industry. Lorem Ipsum has been the finishLorem Ipsum is simply dummy text of the printing and typesetting industry.Lorem Ipsum has been the industry's industry. Lorem Ipsum has been the finish.</p>
  </div>
  <div class="abs redband"><span>Copright text here</span><span>1</span></div>
</section>

<!-- Table -->
<section class="sheet r2 c1">
  <div class="brand" style="right:10px;top:17px">Harbourlane ICT Support</div>
  <div class="abs subtitle" style="left:13px;top:50px;font-size:15px">Subtitle Here</div>
  <p class="abs body" style="left:13px;top:72px;width:350px;height:98px">Lorem Ipsum is simply dummy text of the printing and typesetting industry. Lorem Ipsum has been the industry's industry. Lorem Ipsum has been the finishLorem Ipsum is simply dummy text of the printing and typesetting industry. Lorem Ipsum has been the industry's industry. Lorem Ipsum has been the finishLorem Ipsum is simply dummy text of the printing and typesetting industry. Lorem Ipsum has been the industry's industry. Lorem Ipsum has been the finishLorem Ipsum is simply dummy text of the printing and typesetting industry. Lorem Ipsum has been the industry's industry. Lorem Ipsum has been the finish.</p>
  <table class="table">
    <thead><tr><th>Table Section Title Here</th><th>Table Section Title Here</th><th>Title Here</th></tr></thead>
    <tbody>
      <tr><td>Table Section subtext here</td><td>Table Section subtext here</td><td class="price">$150.00</td></tr>
      <tr><td>Table Section subtext here</td><td>Table Section subtext here</td><td class="price">$150.00</td></tr>
      <tr><td>Table Section subtext here</td><td>Table Section subtext here</td><td class="price">$150.00</td></tr>
      <tr><td>Table Section subtext here</td><td>Table Section subtext here</td><td class="price">$150.00</td></tr>
      <tr><td>Table Section subtext here</td><td>Table Section subtext here</td><td class="price">$150.00</td></tr>
      <tr><td>Table Section subtext here</td><td>Table Section subtext here</td><td class="price">$150.00</td></tr>
      <tr><td>Table Section subtext here</td><td>Table Section subtext here</td><td class="price">$150.00</td></tr>
      <tr><td>Table Section subtext here</td><td>Table Section subtext here</td><td class="price">$150.00</td></tr>
    </tbody>
  </table>
  <p class="abs body" style="left:13px;top:418px;width:350px;height:70px">Lorem Ipsum is simply dummy text of the printing and typesetting industry. Lorem Ipsum has been the industry's industry. Lorem Ipsum has been the finishLorem Ipsum is simply dummy text of the printing and typesetting industry. Lorem Ipsum has been the industry's industry. Lorem Ipsum has been the finishLorem Ipsum is simply dummy text of the printing and typesetting industry. Lorem Ipsum has been the industry's industry.</p>
  <div class="footer">Confendtial <b>2</b></div>
</section>

<!-- Two columns with side panel -->
<section class="sheet r2 c2">
  <div class="brand" style="right:10px;top:17px">Harbourlane ICT Support</div>
  <div class="abs" style="left:21px;top:56px;width:153px">
    <div class="subtitle" style="font-size:10px;line-height:14px">Subtitle Here</div>
    <p class="body" style="height:238px">Lorem Ipsum is simply dummy text of the printing and typesetting industry. Lorem Ipsum has been the industry's industry. Lorem Ipsum has been the finishLorem Ipsum is simply dummy text of the printing and typesetting industry. Lorem Ipsum has been the industry's industry. Lorem Ipsum has been the finishLorem Ipsum is simply dummy text of the printing and typesetting industry. Lorem Ipsum has been the industry's industry. Lorem Ipsum has been the finishLorem Ipsum is simply dummy text of the printing and typesetting industry. Lorem Ipsum has been the industry's industry. Lorem Ipsum has been the finish.</p>
    <p class="body" style="margin-top:14px;height:168px">Lorem Ipsum is simply dummy text of the printing and typesetting industry. Lorem Ipsum has been the industry's industry. Lorem Ipsum has been the finishLorem Ipsum is simply dummy text of the printing and typesetting industry. Lorem Ipsum has been the industry's industry. Lorem Ipsum has been the finishLorem Ipsum is simply dummy text of the printing and typesetting industry. Lorem Ipsum has been the industry's industry.</p>
  </div>
  <p class="abs body" style="left:205px;top:56px;width:153px;height:56px">Lorem Ipsum is simply dummy text of the printing and typesetting industry. Lorem Ipsum has been the industry's industry.</p>
  <p class="abs greybox">Lorem Ipsum is simply dummy text of the printing and typesetting industry. Lorem Ipsum has been the industry's industry. Lorem Ipsum has been the finishLorem Ipsum is simply dummy text of the printing and typesetting industry. Lorem Ipsum has been the industry's industry. Lorem Ipsum is simply dummy text of the printing and typesetting industry. Lorem Ipsum has been the industry's industry.</p>
  <p class="abs body" style="left:205px;top:336px;width:153px;height:140px">Lorem Ipsum has been the finishLorem Ipsum is simply dummy text of the printing and typesetting industry. Lorem Ipsum has been the industry's industry. Lorem Ipsum has been the finishLorem Ipsum is simply dummy text of the printing and typesetting industry. Lorem Ipsum has been the industry's industry. Lorem Ipsum has been the finishLorem Ipsum.</p>
  <div class="footer">Confendtial <b>1</b></div>
</section>

<!-- Callout page -->
<section class="sheet r2 c3">
  <div class="abs redbar"></div>
  <div class="brand" style="right:10px;top:17px">Harbourlane ICT Support</div>
  <div class="abs tealbox"><p>Lorem Ipsum is simply dummy text of the printing and typesetting industry. Lorem Ipsum has been the industry's industry. Lorem Ipsum has been the finishLorem Ipsum is simply dummy text of the printing and typesetting industry. Lorem Ipsum has been the industry's industry. Lorem Ipsum is simply dummy text of the printing and typesetting industry. Lorem Ipsum has been the industry's industry.</p></div>
  <div class="abs" style="left:173px;top:56px;width:190px">
    <div class="subtitle" style="font-size:10px;line-height:14px">Subtitle Here</div>
    <p class="body" style="height:196px">Lorem Ipsum is simply dummy text of the printing and typesetting industry. Lorem Ipsum has been the industry's industry. Lorem Ipsum has been the finishLorem Ipsum is simply dummy text of the printing and typesetting industry. Lorem Ipsum has been the industry's industry. Lorem Ipsum has been the finishLorem Ipsum is simply dummy text of the printing and typesetting industry. Lorem Ipsum has been the industry's industry. Lorem Ipsum has been the finishLorem Ipsum is simply dummy text of the printing and typesetting industry. Lorem Ipsum has been the industry's industry. Lorem Ipsum has been the finish.</p>
    <p class="body" style="margin-top:12px;height:196px">Lorem Ipsum is simply dummy text of the printing and typesetting industry. Lorem Ipsum has been the industry's industry. Lorem Ipsum has been the finishLorem Ipsum is simply dummy text of the printing and typesetting industry. Lorem Ipsum has been the industry's industry. Lorem Ipsum has been the finishLorem Ipsum is simply dummy text of the printing and typesetting industry. Lorem Ipsum has been the industry's industry. Lorem Ipsum has been the finishLorem Ipsum is simply dummy text of the printing and typesetting industry. Lorem Ipsum has been the industry's industry. Lorem Ipsum has been the finish.</p>
  </div>
  <div class="abs tealfoot"></div>
  <div class="footer">Confendtial <b>2</b></div>
</section>

</body>
</html>
```